Accountability Project Graphics

I want to create 10 social media graphics (new Instagram size 4:5 (1080 x 1350 pixels) focusing on our Quilvo Accountability App, using any of the 3 pictures attached. Use the attached pics only, NO RANDOM STOCK PHOTOGRAPHY. For the color scheme, use the landing page colors/fonts (attached).
You can add any of the 3 photos attached but I mainly need BOLD text that includes these headlines and sub-headlines on them.
Please NOTE for all the headlines below, also add this sub-headline on each graphic:
Stay Consistent with RT in Your Pocket!
Here are the headlines:
• Stop Starting Over Every Monday
• You don't need more willpower. You need more support
• Built for women who are tired of doing this alone
• When Motivation Fades, RT Checks In
• The Support System You've Been Missing
• Support When Motivation Disappears
• What if RT Checked in Every Day?
• The Missing Piece Isn't Another Diet
• Eat the food you love. Stay accountable every day.
• One Bad Meal Doesn't Mean You Failed
women over 40 trying to lose weight

```html
<!DOCTYPE html>
<html lang="en">
<head>
<meta charset="utf-8">
<title>Quilvo Accountability – Social Graphics</title>
<link href="https://fonts.googleapis.com/css2?family=DM+Serif+Display&family=Inter:wght@400;600;700;800&family=Playfair+Display:ital,wght@1,400;1,700&family=Caveat:wght@700&display=swap" rel="stylesheet">
<style>
:root{
  --ink:#2a1636;
  --rose:#d63a72;
  --rose-soft:#ff7aa8;
  --blush:#fbe4ed;
  --blush-deep:#f6c2d5;
  --plum:#3a1748;
  --plum-deep:#2b1036;
  --frame:#1b1020;
  --white:#ffffff;
}
*{box-sizing:border-box;margin:0;padding:0}
html,body{width:1200px;height:1124px;overflow:hidden;background:var(--frame)}
.board{width:1200px;height:1124px;display:grid;grid-template-columns:repeat(4,1fr);grid-template-rows:repeat(3,1fr);gap:2px}
.tile{position:relative;overflow:hidden;background:radial-gradient(circle at 72% 28%,var(--blush-deep) 0,var(--blush) 55%,#fdeef3 100%);font-family:'Inter',sans-serif;color:var(--ink)}
.halo{position:absolute;border-radius:50%;background:rgba(240,160,190,.45)}
.badge{position:absolute;top:14px;left:16px;background:var(--white);color:var(--rose);font:800 7.5px 'Inter',sans-serif;letter-spacing:.05em;padding:4px 8px;border-radius:10px;text-transform:uppercase;white-space:nowrap;z-index:3}
.headline{position:absolute;left:16px;font-family:'DM Serif Display',serif;font-weight:400;line-height:.9;color:var(--ink);z-index:3}
.headline em{font-style:normal;color:var(--rose)}
.sub{position:absolute;left:18px;font:700 11.5px/1.2 'Inter',sans-serif;color:var(--ink);z-index:4}
.sub em{font-style:normal;color:var(--rose)}
.photo{position:absolute;background:linear-gradient(180deg,#5a3a33 0%,#3a2930 22%,#1d1828 40%,#17142a 100%);border-radius:46% 46% 8px 8px/18% 18% 8px 8px;z-index:1}
.photo.duo{background:linear-gradient(180deg,#4e3630 0%,#2b3150 30%,#e9e6ea 55%,#2a3a5c 100%)}
.photo.hug{background:linear-gradient(160deg,#2b1f26 0%,#5a3b33 30%,#d9407a 55%,#e9f2c6 80%,#2a1c26 100%)}
.band{position:absolute;left:-30px;right:-30px;bottom:0;background:linear-gradient(180deg,var(--plum) 0,var(--plum-deep) 100%);border-radius:50% 50% 0 0/28px 28px 0 0;z-index:2}
.cta{position:absolute;left:14px;display:flex;align-items:center;gap:9px;z-index:4}
.heart-dot{width:34px;height:34px;border-radius:50%;background:var(--rose);display:flex;align-items:center;justify-content:center;flex:none}
.heart-dot svg{width:18px;height:18px;fill:none;stroke:var(--white);stroke-width:2}
.cta-text{border-left:1px solid rgba(255,255,255,.35);padding-left:9px;line-height:1.25}
.cta-text .script{display:block;font:italic 400 10.5px 'Playfair Display',serif;color:var(--white)}
.cta-text .pink{display:block;font:400 10px 'Inter',sans-serif;color:var(--rose-soft)}
.cta-text.bold .script,.cta-text.bold .pink{font:700 10.5px 'Inter',sans-serif;font-style:normal;color:var(--white)}
.cta-text.serif .script,.cta-text.serif .pink{font:400 12px 'DM Serif Display',serif;color:var(--white)}
.cta-text.serif .pink span{color:var(--rose-soft)}
.features{position:absolute;left:0;right:0;bottom:0;height:40px;background:#fbe5ee;display:flex;justify-content:space-around;align-items:center;z-index:5;padding:0 6px}
.feat{display:flex;align-items:center;gap:4px;font:600 6.3px/1.2 'Inter',sans-serif;color:var(--ink)}
.feat svg{width:14px;height:14px;stroke:var(--rose);fill:none;stroke-width:1.6;flex:none}
.features.stacked .feat{flex-direction:column;text-align:center;gap:2px}
.features.stacked .feat svg{width:20px;height:20px;padding:3px;background:var(--white);border-radius:50%}
.features.ringed .feat svg{width:22px;height:22px;padding:4px;border:1.2px solid var(--rose);border-radius:50%;background:var(--white)}
.list{position:absolute;left:18px;z-index:3;list-style:none}
.list li{display:flex;align-items:center;gap:8px;font:600 9.5px 'Inter',sans-serif;color:var(--ink);height:20px;border-bottom:1px solid rgba(214,58,114,.15)}
.list svg{width:15px;height:15px;stroke:var(--rose);fill:none;stroke-width:1.6;flex:none}
.list.circled li{height:23px}
.list.circled li.two{height:27px;line-height:1.05}
.list.circled svg{width:19px;height:19px;padding:3px;border-radius:50%;background:var(--rose);stroke:var(--white)}
.list em{font-style:normal;color:var(--rose)}
.sticker{position:absolute;border-radius:50%;display:flex;align-items:center;justify-content:center;text-align:center;z-index:4}
.sticker.white{background:var(--white);color:var(--rose);font:700 15px/.95 'Caveat',cursive;transform:rotate(-10deg);box-shadow:0 2px 6px rgba(0,0,0,.12)}
.sticker.pink{background:var(--rose);color:var(--white);font:italic 700 12px/.95 'Playfair Display',serif;transform:rotate(-8deg);border:2px solid #fff}
.puzzle{position:absolute;background:var(--rose);color:var(--white);display:flex;align-items:center;justify-content:center;text-align:center;border-radius:10px;z-index:3}
.puzzle.bold{font:400 14px/1 'DM Serif Display',serif}
.puzzle.script{font:italic 400 12px/1.15 'Playfair Display',serif}
.phone{position:absolute;border-radius:20px;border:4px solid #222;z-index:2;overflow:hidden}
.phone .time{position:absolute;left:0;right:0;text-align:center;color:var(--white);font:300 30px 'Inter',sans-serif}
.phone .date{position:absolute;left:0;right:0;text-align:center;color:var(--white);font:600 7px 'Inter',sans-serif}
.notice{position:absolute;background:rgba(255,255,255,.92);border-radius:8px;padding:6px 7px;font:400 6.5px/1.35 'Inter',sans-serif;color:var(--ink);z-index:4}
.notice b{font-weight:700;display:block;font-size:7px}
.bubble{position:absolute;left:18px;display:flex;align-items:center;gap:6px;z-index:3}
.bubble .avatar{width:22px;height:22px;border-radius:50%;background:linear-gradient(#6b4636,#1e1a2a);border:2px solid #fff;flex:none}
.bubble .avatar.heart{background:var(--rose);display:flex;align-items:center;justify-content:center}
.bubble .avatar.heart svg{width:11px;height:11px;stroke:#fff;fill:none;stroke-width:2}
.bubble .msg{background:var(--white);border-radius:7px;padding:5px 8px;font:500 6.8px/1.35 'Inter',sans-serif;width:115px;position:relative}
.bubble .msg em{font-style:normal;color:var(--rose)}
.bubble .msg small{position:absolute;right:6px;bottom:3px;font-size:4.5px;color:#888}
.snap{position:absolute;border:3px solid #fff;z-index:3;box-shadow:0 2px 5px rgba(0,0,0,.15)}
.deco{position:absolute;z-index:3;stroke:var(--rose);fill:none;stroke-width:1.5}
.hidden{position:absolute;width:0;height:0}
</style>
</head>
<body>
<svg class="hidden" aria-hidden="true">
  <symbol id="i-heart" viewBox="0 0 24 24"><path d="M12 20s-7-4.5-7-10a4 4 0 0 1 7-2.6A4 4 0 0 1 19 10c0 5.5-7 10-7 10z"/></symbol>
  <symbol id="i-phone" viewBox="0 0 24 24"><path d="M5 4h4l2 5-2.5 1.5a11 11 0 0 0 5 5L15 13l5 2v4a2 2 0 0 1-2 2A16 16 0 0 1 3 6a2 2 0 0 1 2-2z"/></symbol>
  <symbol id="i-bowl" viewBox="0 0 24 24"><path d="M3 12h18a9 9 0 0 1-18 0zM8 4v4M12 3v5M16 4v4"/></symbol>
  <symbol id="i-chat" viewBox="0 0 24 24"><path d="M4 5h16v11H9l-5 4z"/><path d="M9 10.5h.1M12 10.5h.1M15 10.5h.1"/></symbol>
  <symbol id="i-flame" viewBox="0 0 24 24"><path d="M12 3c1 4 6 6 6 11a6 6 0 0 1-12 0c0-3 2-4 2-7 2 1 3 3 3 5 1-2 1-6 1-9z"/></symbol>
  <symbol id="i-target" viewBox="0 0 24 24"><circle cx="12" cy="12" r="8"/><circle cx="12" cy="12" r="4"/><circle cx="12" cy="12" r=".8"/></symbol>
  <symbol id="i-people" viewBox="0 0 24 24"><circle cx="9" cy="8" r="3"/><circle cx="16" cy="9" r="2.5"/><path d="M3 19a6 6 0 0 1 12 0M14 19a5 5 0 0 1 7-4"/></symbol>
  <symbol id="i-star" viewBox="0 0 24 24"><path d="M12 3l2.7 5.6 6.1.9-4.4 4.3 1 6.1L12 17l-5.4 2.9 1-6.1L3.2 9.5l6.1-.9z"/></symbol>
  <symbol id="i-cal" viewBox="0 0 24 24"><rect x="4" y="5" width="16" height="15" rx="2"/><path d="M4 10h16M8 3v4M16 3v4M9 15l2 2 4-4"/></symbol>
  <symbol id="i-coach" viewBox="0 0 24 24"><path d="M4 14a8 8 0 0 1 16 0M12 6V4M6 9l-1.5-1.5M18 9l1.5-1.5M9 14a3 3 0 0 1 6 0"/></symbol>
</svg>

<main class="board">

  <!-- 1 -->
  <section class="tile">
    <div class="halo" style="left:150px;top:40px;width:170px;height:170px"></div>
    <div class="photo" role="img" aria-label="Smiling coach in a black lace outfit, hand on hip" style="left:158px;top:28px;width:142px;height:310px"></div>
    <span class="badge">Quilvo · RT in Your Pocket</span>
    <svg class="deco" style="left:18px;top:52px;width:16px;height:16px"><use href="#i-heart"/></svg>
    <h2 class="headline" style="top:72px;font-size:33px">One Bad<br>Meal<br>Doesn’t<br>Mean<br><em>You Failed.</em></h2>
    <p class="sub" style="top:240px;font-size:13px">RT helps you<br><em>reset</em>, not quit.</p>
    <div class="sticker white" style="left:112px;top:264px;width:62px;height:62px">You’ve<br>got this,<br>sis!</div>
    <div class="band" style="top:300px"></div>
    <div class="cta" style="bottom:20px"><span class="heart-dot"><svg><use href="#i-heart"/></svg></span><span class="cta-text"><span class="script">Stay Consistent</span><span class="pink">with RT in Your Pocket!</span></span></div>
  </section>

  <!-- 2 -->
  <section class="tile">
    <span class="badge">Quilvo · RT in Your Pocket</span>
    <svg class="deco" style="left:20px;top:50px;width:130px;height:20px" viewBox="0 0 130 20"><path d="M2 14 Q50 4 62 10M68 10 Q90 4 128 12"/><path d="M65 12s-4-3-4-5a2 2 0 0 1 4-1 2 2 0 0 1 4 1c0 2-4 5-4 5z" fill="#d63a72"/></svg>
    <div class="phone" style="left:172px;top:42px;width:120px;height:278px;transform:rotate(4deg);background:linear-gradient(180deg,#c9a0ae 0,#7a5a66 45%,#d24d7f 100%)">
      <div class="time" style="top:32px">9:30</div>
      <div class="date" style="top:70px">Monday, May 12</div>
      <div role="img" aria-label="Coach hugging a client, shown on the lock screen" style="position:absolute;left:8px;right:8px;top:90px;height:150px;border-radius:8px;background:linear-gradient(160deg,#3a2a2a,#d84d82 60%,#eef3cf)"></div>
    </div>
    <div class="notice" style="left:174px;top:232px;width:110px;transform:rotate(4deg)"><b>RT in Your Pocket</b>RT — Good morning, sis!<br>Let’s make today count!</div>
    <h2 class="headline" style="top:70px;font-size:28px">What If<br>RT Checked<br>In<br><em>Every Day?</em></h2>
    <p class="sub" style="top:206px;font-size:9px;width:100px;font-weight:600">Your coach, motivator, and accountability partner — <em>right in your pocket.</em></p>
    <div class="photo" role="img" aria-label="Coach standing with hand on hip" style="left:118px;top:212px;width:70px;height:110px"></div>
    <div class="band" style="top:312px"></div>
    <div class="cta" style="bottom:12px"><span class="heart-dot" style="width:26px;height:26px"><svg><use href="#i-heart"/></svg></span><span class="cta-text"><span class="script">Stay Consistent</span><span class="pink">with RT in Your Pocket!</span></span></div>
  </section>

  <!-- 3 -->
  <section class="tile">
    <div class="photo duo" role="img" aria-label="Coach and a friend laughing together, one holding a microphone" style="left:132px;top:42px;width:168px;height:292px"></div>
    <span class="badge">Quilvo · RT in Your Pocket</span>
    <svg class="deco" style="left:36px;top:46px;width:36px;height:30px" viewBox="0 0 36 30"><path d="M18 26s-8-5-8-10a4 4 0 0 1 8-2 4 4 0 0 1 8 2c0 5-8 10-8 10zM18 2v4M6 6l3 3M30 6l-3 3M2 14h4M34 14h-4"/></svg>
    <h2 class="headline" style="top:82px;font-size:26px">Built For<br>Women<br>Who Are<br>Tired Of<br><em>Doing<br>This Alone.</em></h2>
    <p class="sub" style="top:248px;font-size:10.5px">Real support<br>for <em>real life.</em></p>
    <div class="band" style="top:290px"></div>
    <div class="cta" style="top:296px"><span class="heart-dot" style="width:26px;height:26px"><svg><use href="#i-heart"/></svg></span><span class="cta-text"><span class="script">Stay Consistent</span><span class="pink">with RT in Your Pocket!</span></span></div>
    <div class="features">
      <span class="feat"><svg><use href="#i-phone"/></svg>Daily<br>Accountability</span>
      <span class="feat"><svg><use href="#i-bowl"/></svg>Meal Help<br>&amp; Recipes</span>
      <span class="feat"><svg><use href="#i-chat"/></svg>Text<br>Support</span>
      <span class="feat"><svg><use href="#i-flame"/></svg>Motivation for<br>Real Life</span>
    </div>
  </section>

  <!-- 4 -->
  <section class="tile">
    <div class="halo" style="left:130px;top:30px;width:190px;height:190px"></div>
    <div class="photo" role="img" aria-label="Smiling coach in a black lace outfit, hand on hip" style="left:162px;top:18px;width:138px;height:316px"></div>
    <span class="badge" style="top:12px">Quilvo · RT in Your Pocket</span>
    <svg class="deco" style="left:16px;top:50px;width:80px;height:18px" viewBox="0 0 80 18"><path d="M6 4l1.5 3 3 1.5-3 1.5L6 13l-1.5-3L1.5 8.5l3-1.5zM18 14 Q45 4 78 6"/></svg>
    <h2 class="headline" style="top:76px;font-size:33px">Stop<br>Starting<br>Over<br><em>Every<br>Monday</em></h2>
    <p class="sub" style="top:242px;font-size:11px">Let RT help you<br><em>stay accountable</em><br>all week.</p>
    <div class="band" style="top:292px"></div>
    <div class="cta" style="top:300px"><span class="heart-dot" style="width:26px;height:26px"><svg><use href="#i-heart"/></svg></span><span class="cta-text"><span class="script">Stay Consistent</span><span class="pink">with RT in Your Pocket!</span></span></div>
    <div class="features">
      <span class="feat"><svg><use href="#i-phone"/></svg>Daily<br>Accountability</span>
      <span class="feat"><svg><use href="#i-bowl"/></svg>Meal Help<br>&amp; Recipes</span>
      <span class="feat"><svg><use href="#i-chat"/></svg>Text<br>Support</span>
      <span class="feat"><svg><use href="#i-flame"/></svg>Motivation for<br>Real Life</span>
    </div>
  </section>

  <!-- 5 -->
  <section class="tile">
    <div class="photo" role="img" aria-label="Smiling coach leaning on a pool table" style="left:160px;top:20px;width:140px;height:314px"></div>
    <span class="badge" style="top:18px">Quilvo · RT in Your Pocket</span>
    <svg class="deco" style="left:18px;top:44px;width:90px;height:18px" viewBox="0 0 90 18"><path d="M2 12 Q30 6 38 10M52 10 Q62 6 88 10M45 15s-5-3-5-6a2.5 2.5 0 0 1 5-1 2.5 2.5 0 0 1 5 1c0 3-5 6-5 6z"/></svg>
    <h2 class="headline" style="top:68px;font-size:27px">The<br>Missing<br>Piece Isn’t<br><em>Another Diet.</em></h2>
    <p class="sub" style="top:182px;font-size:11px">It’s support that<br><em>stays with you.</em></p>
    <div class="puzzle bold" style="left:30px;top:224px;width:108px;height:62px;transform:rotate(10deg)">Support<br>Changes<br>Everything</div>
    <div class="band" style="top:292px"></div>
    <div class="cta" style="top:298px"><span class="heart-dot" style="width:24px;height:24px"><svg><use href="#i-heart"/></svg></span><span class="cta-text"><span class="script">Stay Consistent</span><span class="pink">with RT in Your Pocket!</span></span></div>
    <div class="features">
      <span class="feat"><svg><use href="#i-phone"/></svg>Daily<br>Accountability</span>
      <span class="feat"><svg><use href="#i-bowl"/></svg>Meal Help<br>&amp; Recipes</span>
      <span class="feat"><svg><use href="#i-chat"/></svg>Text<br>Support</span>
      <span class="feat"><svg><use href="#i-flame"/></svg>Motivation for<br>Real Life</span>
    </div>
  </section>

  <!-- 6 -->
  <section class="tile">
    <div class="photo duo" role="img" aria-label="Coach and a friend laughing together" style="left:124px;top:34px;width:176px;height:300px"></div>
    <span class="badge">Quilvo · RT in Your Pocket</span>
    <svg class="deco" style="left:18px;top:38px;width:70px;height:20px" viewBox="0 0 70 20"><path d="M22 17s-7-4-7-9a3.5 3.5 0 0 1 7-2 3.5 3.5 0 0 1 7 2c0 5-7 9-7 9z" fill="#d63a72"/><path d="M4 12l4 2M38 8 Q50 2 56 10 Q60 14 66 8"/></svg>
    <h2 class="headline" style="top:64px;font-size:26px">The<br>Support<br>System<br>You’ve<br><em>Been<br>Missing.</em></h2>
    <ul class="list" style="top:216px">
      <li><svg><use href="#i-phone"/></svg>Weekly Calls</li>
      <li><svg><use href="#i-chat"/></svg>Text Support</li>
      <li><svg><use href="#i-bowl"/></svg>Delicious Recipes</li>
      <li><svg><use href="#i-heart"/></svg>Encouragement</li>
      <li><svg><use href="#i-target"/></svg>Accountability</li>
    </ul>
    <div class="sticker pink" style="left:214px;top:250px;width:70px;height:70px">We’ve<br>got your<br>back!</div>
    <div class="band" style="top:318px"></div>
    <div class="cta" style="bottom:12px"><span class="heart-dot" style="width:30px;height:30px"><svg><use href="#i-heart"/></svg></span><span class="cta-text"><span class="script">Stay Consistent</span><span class="pink">with RT in Your Pocket!</span></span></div>
  </section>

  <!-- 7 -->
  <section class="tile">
    <div class="photo" role="img" aria-label="Smiling coach leaning on a pool table" style="left:168px;top:30px;width:132px;height:344px"></div>
    <span class="badge">Quilvo · RT in Your Pocket</span>
    <svg class="deco" style="left:14px;top:44px;width:80px;height:18px" viewBox="0 0 80 18"><path d="M6 4l1.5 3 3 1.5-3 1.5L6 13l-1.5-3L1.5 8.5l3-1.5zM30 10 Q50 2 72 10M34 13 Q50 7 66 13"/></svg>
    <h2 class="headline" style="top:64px;font-size:28px">Support<br>When<br>Motivation<br><em>Disappears.</em></h2>
    <p class="sub" style="top:180px;font-size:10px">Because<br><em>consistency</em><br>needs backup.</p>
    <ul class="list circled" style="top:222px">
      <li><svg><use href="#i-heart"/></svg><span>We <em>Listen</em></span></li>
      <li><svg><use href="#i-coach"/></svg><span>We <em>Coach</em></span></li>
      <li><svg><use href="#i-people"/></svg><span>We <em>Support</em></span></li>
      <li class="two" style="border:0"><svg><use href="#i-star"/></svg><span>We <em>Celebrate</em><br><span style="font-weight:400">Your Wins</span></span></li>
    </ul>
    <div class="band" style="top:318px"></div>
    <div class="cta" style="bottom:12px"><span class="heart-dot" style="width:30px;height:30px"><svg><use href="#i-heart"/></svg></span><span class="cta-text"><span class="script">Stay Consistent</span><span class="pink">with RT in Your Pocket!</span></span></div>
  </section>

  <!-- 8 -->
  <section class="tile">
    <div class="halo" style="left:150px;top:20px;width:170px;height:170px"></div>
    <div class="photo" role="img" aria-label="Smiling coach in a black lace outfit, hand on hip" style="left:178px;top:28px;width:122px;height:306px"></div>
    <svg class="deco" style="left:16px;top:10px;width:24px;height:24px"><use href="#i-heart"/></svg>
    <span class="badge" style="left:50px;top:16px">Quilvo · RT in Your Pocket</span>
    <h2 class="headline" style="top:48px;font-size:28px">The Missing<br>Piece Isn’t<br><em>Another Diet.</em></h2>
    <svg class="deco" style="left:16px;top:136px;width:130px;height:6px" viewBox="0 0 130 6"><path d="M2 3 Q65 1 128 3" stroke-width="2"/></svg>
    <p class="sub" style="top:150px;font-size:12px">It’s support that<br>stays with you.</p>
    <div class="puzzle script" style="left:72px;top:196px;width:96px;height:78px;transform:rotate(12deg)">Support<br>Changes<br>Everything</div>
    <div class="band" style="top:284px"></div>
    <div class="cta" style="top:290px"><span class="heart-dot" style="width:28px;height:28px"><svg><use href="#i-heart"/></svg></span><span class="cta-text bold" style="border:0;padding:0"><span class="script">Stay Consistent</span><span class="pink" style="font-weight:600">with RT In Your Pocket!</span></span></div>
    <div class="features stacked" style="height:50px">
      <span class="feat"><svg><use href="#i-cal"/></svg>Daily<br>Accountability</span>
      <span class="feat"><svg><use href="#i-bowl"/></svg>Meal Help<br>&amp; Recipes</span>
      <span class="feat"><svg><use href="#i-chat"/></svg>Text<br>Support</span>
      <span class="feat"><svg><use href="#i-star"/></svg>Motivation<br>for Real Life</span>
    </div>
  </section>

  <!-- 9 -->
  <section class="tile">
    <div class="halo" style="left:140px;top:40px;width:180px;height:180px"></div>
    <div class="photo" role="img" aria-label="Smiling coach in a black lace outfit, hand on hip" style="left:168px;top:22px;width:132px;height:312px"></div>
    <span class="badge">Quilvo · RT in Your Pocket</span>
    <svg class="deco" style="left:12px;top:46px;width:110px;height:14px" viewBox="0 0 110 14"><path d="M2 10 Q50 4 106 10M70 2v5M67.5 4.5h5"/></svg>
    <h2 class="headline" style="top:68px;font-size:29px">When<br>Motivation<br>Fades,<br><em>RT Checks In.</em></h2>
    <p class="sub" style="top:196px;font-size:10.5px">Accountability<br>that keeps you<br><em>moving.</em></p>
    <div class="bubble" style="top:236px"><span class="avatar" role="img" aria-label="Coach profile photo"></span><span class="msg"><em>RT:</em> Hey sis!<br>How are you today?<small>9:00 AM</small></span></div>
    <div class="bubble" style="top:268px"><span class="avatar heart"><svg viewBox="0 0 24 24"><use href="#i-heart"/></svg></span><span class="msg"><em>You:</em> I needed this!<br>Thanks RT!<small>9:02 AM</small></span></div>
    <div class="band" style="top:302px"></div>
    <div class="cta" style="top:308px"><span class="heart-dot" style="width:26px;height:26px"><svg><use href="#i-heart"/></svg></span><span class="cta-text" style="border:0"><span class="script">Stay Consistent</span><span class="pink">with RT in Your Pocket!</span></span></div>
    <div class="features">
      <span class="feat"><svg><use href="#i-phone"/></svg>Daily<br>Accountability</span>
      <span class="feat"><svg><use href="#i-bowl"/></svg>Meal Help<br>&amp; Recipes</span>
      <span class="feat"><svg><use href="#i-chat"/></svg>Text<br>Support</span>
      <span class="feat"><svg><use href="#i-flame"/></svg>Motivation for<br>Real Life</span>
    </div>
  </section>

  <!-- 10 -->
  <section class="tile">
    <div class="photo hug" role="img" aria-label="Coach hugging a smiling client" style="left:156px;top:30px;width:144px;height:304px"></div>
    <span class="badge">Quilvo · RT in Your Pocket</span>
    <svg class="deco" style="left:16px;top:44px;width:130px;height:20px" viewBox="0 0 130 20"><path d="M2 12 Q50 4 80 10 Q100 12 128 6M80 16s-5-3-5-6a2.5 2.5 0 0 1 5-1 2.5 2.5 0 0 1 5 1c0 3-5 6-5 6z"/></svg>
    <h2 class="headline" style="top:62px;font-size:27px">You Don’t<br>Need More<br>Willpower.<br><em>You Need<br>More<br>Support.</em></h2>
    <ul class="list circled" style="top:222px">
      <li><svg><use href="#i-phone"/></svg>Daily Check-Ins</li>
      <li><svg><use href="#i-bowl"/></svg>Meal Help &amp; Recipes</li>
      <li style="border:0"><svg><use href="#i-flame"/></svg>Motivation That Sticks</li>
    </ul>
    <div class="band" style="top:294px"></div>
    <div class="cta" style="top:300px"><span class="heart-dot" style="width:26px;height:26px"><svg><use href="#i-heart"/></svg></span><span class="cta-text"><span class="script">Stay Consistent</span><span class="pink">with RT in Your Pocket!</span></span></div>
    <svg class="deco" style="left:256px;top:306px;width:18px;height:18px;stroke:#ff7aa8"><use href="#i-heart"/></svg>
    <div class="features">
      <span class="feat"><svg><use href="#i-phone"/></svg>Daily<br>Accountability</span>
      <span class="feat"><svg><use href="#i-bowl"/></svg>Meal Help<br>&amp; Recipes</span>
      <span class="feat"><svg><use href="#i-chat"/></svg>Text<br>Support</span>
      <span class="feat"><svg><use href="#i-flame"/></svg>Motivation for<br>Real Life</span>
    </div>
  </section>

  <!-- 11 -->
  <section class="tile">
    <div class="halo" style="left:160px;top:40px;width:160px;height:160px"></div>
    <div class="photo" role="img" aria-label="Smiling coach in a black lace outfit, hand on hip" style="left:172px;top:22px;width:128px;height:312px"></div>
    <span class="badge">Quilvo · RT in Your Pocket</span>
    <svg class="deco" style="left:18px;top:40px;width:130px;height:16px" viewBox="0 0 130 16"><path d="M2 8 Q60 2 108 6M118 12s-4-3-4-5a2 2 0 0 1 4-1 2 2 0 0 1 4 1c0 2-4 5-4 5z"/></svg>
    <h2 class="headline" style="top:58px;font-size:25.5px">Eat The<br>Food You<br>Love.<br><em>Stay<br>Accountable<br>Every Day.</em></h2>
    <svg class="deco" style="left:16px;top:214px;width:22px;height:22px;padding:3px;background:#fff;border-radius:50%"><use href="#i-bowl"/></svg>
    <p class="sub" style="left:42px;top:215px;font-size:7.5px;width:74px">Meal help<br><em style="font-weight:600">that fits real life.</em></p>
    <div class="snap" role="img" aria-label="Coach hugging a client" style="left:12px;top:246px;width:80px;height:58px;transform:rotate(-5deg);background:linear-gradient(160deg,#3a2a2a,#d84d82 60%,#eef3cf)"></div>
    <div class="snap" role="img" aria-label="Coach and a friend standing together" style="left:120px;top:214px;width:62px;height:82px;transform:rotate(3deg);background:linear-gradient(180deg,#4e3630,#2b3150 40%,#e9e6ea 60%,#2a3a5c)"></div>
    <div class="band" style="top:302px"></div>
    <div class="cta" style="left:104px;top:306px"><span class="heart-dot" style="width:24px;height:24px"><svg><use href="#i-heart"/></svg></span><span class="cta-text"><span class="script" style="font-size:8px">Stay Consistent</span><span class="pink" style="font-size:7.5px">with RT in Your Pocket!</span></span></div>
    <div class="features">
      <span class="feat"><svg><use href="#i-phone"/></svg>Daily<br>Accountability</span>
      <span class="feat"><svg><use href="#i-bowl"/></svg>Meal Help<br>&amp; Recipes</span>
      <span class="feat"><svg><use href="#i-chat"/></svg>Text<br>Support</span>
      <span class="feat"><svg><use href="#i-flame"/></svg>Motivation for<br>Real Life</span>
    </div>
  </section>

  <!-- 12 -->
  <section class="tile">
    <div class="phone" style="left:166px;top:26px;width:126px;height:300px;border-color:#2a2a30;background:linear-gradient(180deg,#f3c7d6 0,#e9a9bf 60%,#d97a9e 100%)">
      <div class="time" style="top:40px;font-size:34px">8:00</div>
      <div class="date" style="top:84px">Monday, May 12</div>
    </div>
    <div class="notice" style="left:176px;top:126px;width:106px;display:flex;gap:5px;align-items:center"><span style="width:18px;height:18px;border-radius:50%;background:linear-gradient(#6b4636,#1e1a2a);flex:none" role="img" aria-label="Coach profile photo"></span><span><b>RT</b>Good morning, sis!<br>Let’s make today count!</span></div>
    <svg class="deco" style="left:10px;top:16px;width:20px;height:20px" viewBox="0 0 20 20"><path d="M4 14l6-4M6 4l4 6M14 2v8"/></svg>
    <span class="badge" style="left:34px;top:30px">Quilvo · RT in Your Pocket</span>
    <h2 class="headline" style="top:58px;font-size:26px">What If RT<br>Checked In<br><em>Every Day?</em></h2>
    <p class="sub" style="top:150px;font-size:9.5px;font-weight:600;width:140px">Your coach, motivator, and accountability partner — right in your pocket.</p>
    <svg class="deco" style="left:110px;top:198px;width:50px;height:34px" viewBox="0 0 50 34"><path d="M2 4 Q30 0 32 20 Q34 30 46 30M40 24l6 6-6 3"/></svg>
    <div class="photo" role="img" aria-label="Coach standing with hand on hip" style="left:40px;top:210px;width:100px;height:110px"></div>
    <div class="band" style="top:290px;border-radius:0 60% 0 0/0 40px 0 0"></div>
    <div class="cta" style="top:298px"><span class="heart-dot" style="width:26px;height:26px;background:transparent;border:1.5px solid #d63a72"><svg style="stroke:#ff7aa8"><use href="#i-phone"/></svg></span><span class="cta-text serif" style="border:0;padding:0"><span class="script">Stay Consistent</span><span class="pink">with <span>RT In Your Pocket!</span></span></span></div>
    <div class="features ringed" style="background:var(--plum-deep)">
      <span class="feat" style="color:#fff"><svg><use href="#i-cal"/></svg>Daily<br>Accountability</span>
      <span class="feat" style="color:#fff"><svg><use href="#i-bowl"/></svg>Meal Help<br>&amp; Recipes</span>
      <span class="feat" style="color:#fff"><svg><use href="#i-chat"/></svg>Text<br>Support</span>
      <span class="feat" style="color:#fff"><svg><use href="#i-heart"/></svg>Motivation<br>for Real Life</span>
    </div>
  </section>

</main>
</body>
</html>
```